Velundra Jobs portal

Velundra Jobs is a job portal connecting job seekers and companies offering part time jobs in the Mena region, starting in the UAE. We would like to see designs that use the color blue. We have attached images to give an idea what the website should look like. When a company posts a job the job seekers are not allowed to see which company has posted a job. There should also be a coinvex gateway. On the landing page we want a catching picture that we will send.

Target Market(s)

Students and promotional workers

Logo Text

Velundra Jobs

Coding

Coded - Design and coding required

Number of Pages Required

4 page

Font styles to use
Sans Serif

Colors
33a6d7
0692cd
85cae6

```html
<!DOCTYPE html>
<html lang="en">
<head>
<meta charset="utf-8">
<title>Velundra Jobs</title>
<link href="https://fonts.googleapis.com/css2?family=Open+Sans:wght@400;600&family=Nunito:wght@600&display=swap" rel="stylesheet">
<style>
:root{
  --blue:#1ea4ec;
  --link:#1a9be0;
  --text:#222;
  --muted:#777;
  --page:#f2f2f2;
  --card:#fff;
  --line:#ececec;
  --dark:#2b2b2b;
}
*{box-sizing:border-box;margin:0;padding:0}
html,body{width:1146px;height:1200px;overflow:hidden}
body{font-family:"Open Sans",Arial,sans-serif;background:var(--page);color:var(--text);position:relative;font-size:12px}
.abs{position:absolute}
.header{left:0;top:0;width:1146px;height:104px;background:#fafbfc}
.logo{left:66px;top:29px;width:188px;height:64px;background:#fff;display:flex;align-items:center;justify-content:center;font-family:"Nunito",sans-serif;font-size:40px;color:#2fb3c6;letter-spacing:-1px}
.nav{top:54px;font-size:12.5px;color:#555}
.avatar{left:933px;top:37px;width:40px;height:40px;border-radius:50%;background:radial-gradient(circle at 50% 40%,#e8d6c2,#b99a7c);border:2px solid #eee}
.logout{left:998px;top:41px;width:71px;height:30px;background:var(--blue);color:#fff;font-size:12.5px;display:flex;align-items:center;justify-content:center;border-radius:2px}
.bell-badge{left:889px;top:47px;width:14px;height:14px;border-radius:50%;background:var(--blue);color:#fff;font-size:8px;display:flex;align-items:center;justify-content:center}
.hero{left:0;top:104px;width:1146px;height:268px;background:linear-gradient(180deg,#3f4f5e 0%,#55626c 55%,#6e6a68 100%)}
.searchbar{left:158px;top:217px;width:832px;height:51px;background:rgba(160,160,160,.55)}
.field{top:223px;height:40px;background:#fff;font-size:11px;color:#777;display:flex;align-items:center;justify-content:space-between;padding:0 14px}
.field svg{width:8px;height:6px}
.filter{left:845px;top:225px;width:131px;height:37px;background:linear-gradient(#2db3f7,#1698e6);color:#fff;font-size:15px;display:flex;align-items:center;justify-content:center}
.sidebar{left:74px;top:394px;width:212px;height:486px;background:var(--card)}
.sidebar h3{font-weight:400;font-size:13px;text-align:center;height:52px;line-height:60px;border-bottom:1px solid var(--line)}
.cat{display:flex;justify-content:space-between;padding:0 20px 0 24px;height:30.6px;align-items:center;border-bottom:1px solid var(--line);font-size:11.5px}
.cat a{color:var(--link);text-decoration:none}
.cat span{color:var(--muted)}
.cat:last-child{border:none}
.main{left:296px;top:394px;width:774px;height:488px;background:var(--card)}
.intro{position:absolute;left:36px;top:26px;font-size:12.5px}
.intro span{color:var(--link)}
.thead{position:absolute;left:0;top:59px;width:774px;height:45px;background:linear-gradient(#3ec3f8,#1aa0ea);color:#fff;font-size:12.5px;display:flex}
.thead div{display:flex;align-items:center;justify-content:center;border-right:1px solid rgba(255,255,255,.35)}
.row{position:absolute;left:0;width:774px;border-bottom:1px solid var(--line);display:flex;align-items:center}
.row:last-child{border:none}
.jt{width:228px;padding-left:27px;font-size:11px;line-height:20.5px}
.meta{display:flex;gap:14px;color:#777;margin-top:9px;align-items:center}
.meta span{display:flex;align-items:center;gap:5px}
.due{width:153px;text-align:center;font-size:11px;padding-left:10px}
.prov{width:203px;text-align:center;font-size:11px;padding-left:20px}
.apply{margin-left:56px;width:104px;height:33px;background:linear-gradient(#8a8a8a,#686868);color:#fff;font-size:11.5px;font-weight:600;display:flex;align-items:center;justify-content:center;border-radius:2px}
.brandcard{left:78px;top:916px;width:149px;height:182px;background:#fff;box-shadow:0 0 4px rgba(0,0,0,.1)}
.brandart{position:absolute;left:30px;top:14px;width:90px;height:110px;background:linear-gradient(135deg,#8fd6df,#4f8fd0 60%,#d46b8f);border-radius:8px}
.brandname{position:absolute;left:0;width:149px;top:126px;text-align:center;font-family:"Nunito",sans-serif;font-size:27px;color:#2fb3c6}
.feat-title{left:300px;top:920px;color:var(--link);font-size:12.5px}
.partner{top:960px;width:186px;height:140px;background:#e6e6e6;padding:5px}
.partner div{width:100%;height:100%}
.footer{left:0;top:1140px;width:1146px;height:60px;background:var(--dark);color:#fff;font-size:11.5px}
.footer .l{position:absolute;left:48px;top:20px}
.footer .r{position:absolute;right:51px;top:20px}
</style>
</head>
<body>
<header class="abs header"></header>
<div class="abs logo">velundra</div>
<div class="abs nav" style="left:300px">About Us</div>
<div class="abs nav" style="left:379px">Contact Us</div>
<svg class="abs" style="left:832px;top:49px" width="22" height="22" viewBox="0 0 22 22"><circle cx="9" cy="9" r="6.5" fill="none" stroke="#444" stroke-width="2.6"/><line x1="14" y1="14" x2="19" y2="19" stroke="#444" stroke-width="3" stroke-linecap="round"/></svg>
<svg class="abs" style="left:880px;top:50px" width="20" height="22" viewBox="0 0 20 22"><path d="M10 2c-4 0-6 3-6 6v5l-2 3h16l-2-3V8c0-3-2-6-6-6z" fill="none" stroke="#555" stroke-width="1.6"/><path d="M8 18a2 2 0 0 0 4 0" fill="none" stroke="#555" stroke-width="1.6"/></svg>
<div class="abs bell-badge">23</div>
<div class="abs avatar" role="img" aria-label="User profile photo"></div>
<div class="abs logout">Log Out</div>

<div class="abs hero" role="img" aria-label="Photo of a group of business professionals"></div>
<div class="abs searchbar"></div>
<div class="abs field" style="left:163px;width:267px">Skills , Designations, Companies <svg viewBox="0 0 8 6"><path d="M1 1l3 3 3-3" stroke="#777" fill="none"/></svg></div>
<div class="abs field" style="left:438px;width:194px">Location <svg viewBox="0 0 8 6"><path d="M1 1l3 3 3-3" stroke="#777" fill="none"/></svg></div>
<div class="abs field" style="left:639px;width:194px">Total years of Experience <svg viewBox="0 0 8 6"><path d="M1 1l3 3 3-3" stroke="#777" fill="none"/></svg></div>
<div class="abs filter">Filter Jobs</div>

<aside class="abs sidebar">
  <h3>Browse Job by Categories</h3>
  <div class="cat"><a>Freelancers</a><span>(33)</span></div>
  <div class="cat"><a>Full Time Jobs</a><span>(23)</span></div>
  <div class="cat"><a>Non-Profit NGOs</a><span>(10)</span></div>
  <div class="cat"><a>Part Time Jobs</a><span>(15)</span></div>
  <div class="cat"><a>Placement - HR</a><span>(27)</span></div>
  <div class="cat"><a>BPO / Call Centre</a><span>(18)</span></div>
  <div class="cat"><a>Web design</a><span>(27)</span></div>
  <div class="cat"><a>IT Jobs</a><span>(72)</span></div>
  <div class="cat"><a>Placement - trainee</a><span>(27)</span></div>
  <div class="cat"><a>Summer Trainees - Interns</a><span>(27)</span></div>
  <div class="cat"><a>Work From Home</a><span>(27)</span></div>
  <div class="cat"><a>Other Jobs</a><span>(1572)</span></div>
</aside>

<section class="abs main">
  <div class="intro">Looking for Job ? <span>Apply your perfect jobs under following categories</span></div>
  <div class="thead">
    <div style="width:228px">Job Title</div>
    <div style="width:153px">Due Date</div>
    <div style="width:203px">Provider Name</div>
    <div style="flex:1;border:none"></div>
  </div>
  <div class="row" style="top:104px;height:125px">
    <div class="jt">C++ - Technical Lead Openings @<br>Product Client - Hyd
      <div class="meta"><span><svg width="7" height="10" viewBox="0 0 7 10"><path d="M3.5 0A3.5 3.5 0 0 0 0 3.5C0 6 3.5 10 3.5 10S7 6 7 3.5A3.5 3.5 0 0 0 3.5 0z" fill="#1ea4ec"/><circle cx="3.5" cy="3.5" r="1.3" fill="#fff"/></svg>Hyderabad</span><span><svg width="12" height="10" viewBox="0 0 12 10"><rect x="0" y="2" width="12" height="8" rx="1" fill="#1ea4ec"/><rect x="4" y="0" width="4" height="3" fill="none" stroke="#1ea4ec"/></svg>1-2 years</span></div></div>
    <div class="due">23/ 05/ 2015</div><div class="prov">Confidential Employer</div><div class="apply">Apply Now</div>
  </div>
  <div class="row" style="top:229px;height:120px">
    <div class="jt">C++ - Technical Lead Openings @<br>Product Client - Hyd
      <div class="meta"><span><svg width="7" height="10" viewBox="0 0 7 10"><path d="M3.5 0A3.5 3.5 0 0 0 0 3.5C0 6 3.5 10 3.5 10S7 6 7 3.5A3.5 3.5 0 0 0 3.5 0z" fill="#1ea4ec"/><circle cx="3.5" cy="3.5" r="1.3" fill="#fff"/></svg>Hyderabad</span><span><svg width="12" height="10" viewBox="0 0 12 10"><rect x="0" y="2" width="12" height="8" rx="1" fill="#1ea4ec"/><rect x="4" y="0" width="4" height="3" fill="none" stroke="#1ea4ec"/></svg>1-2 years</span></div></div>
    <div class="due">23/ 05/ 2015</div><div class="prov">Confidential Employer</div><div class="apply">Apply Now</div>
  </div>
  <div class="row" style="top:349px;height:120px">
    <div class="jt">C++ - Technical Lead Openings @<br>Product Client - Hyd
      <div class="meta"><span><svg width="7" height="10" viewBox="0 0 7 10"><path d="M3.5 0A3.5 3.5 0 0 0 0 3.5C0 6 3.5 10 3.5 10S7 6 7 3.5A3.5 3.5 0 0 0 3.5 0z" fill="#1ea4ec"/><circle cx="3.5" cy="3.5" r="1.3" fill="#fff"/></svg>Hyderabad</span><span><svg width="12" height="10" viewBox="0 0 12 10"><rect x="0" y="2" width="12" height="8" rx="1" fill="#1ea4ec"/><rect x="4" y="0" width="4" height="3" fill="none" stroke="#1ea4ec"/></svg>1-2 years</span></div></div>
    <div class="due">23/ 05/ 2015</div><div class="prov">Confidential Employer</div><div class="apply">Apply Now</div>
  </div>
</section>

<div class="abs brandcard">
  <div class="brandart" role="img" aria-label="Brand mascot illustration"></div>
  <div class="brandname">velundra</div>
</div>
<div class="abs feat-title">Featured Job Providers</div>
<div class="abs partner" style="left:297px"><div role="img" aria-label="Anonymous provider tile" style="background:#fff"></div></div>
<div class="abs partner" style="left:492px"><div role="img" aria-label="Anonymous provider tile" style="background:#1f4e99"></div></div>
<div class="abs partner" style="left:687px"><div role="img" aria-label="Anonymous provider tile" style="background:#fff"></div></div>
<div class="abs partner" style="left:882px"><div role="img" aria-label="Anonymous provider tile" style="background:#000"></div></div>

<footer class="abs footer">
  <div class="l">Copyright © 2015. VELUNDRA. All rights reserved</div>
  <div class="r">About Us - Terms &amp; Conditions - Site Map</div>
</footer>
</body>
</html>
```